Construction company business card

One side to be the logo with the company name, The other side I would like: (Tomas verbick) Project manager 41 barrow crescent hallam 52917306224783(03) 9703 2428Info@gudeljgroup.comAnd then maybe a couple dot points saying what we do:Construction (commercial & industrial) Civil construction

Anything else please contact me!
Maybe curved st one edge of the card

Target Market(s)

Older clientele

Industry/Entity Type

Construction Company

Contact Information for Business Card

Read above

Colors
3277b5
1b1b1b
9d9d9d

Requirements
Must have
• Use my logo on one side
Nice to have
• Read above
Should not have
• Read above

```html
<!DOCTYPE html>
<html lang="en">
<head>
<meta charset="utf-8">
<title>Stonebay Property Group – Business Card</title>
<link rel="stylesheet" href="https://fonts.googleapis.com/css2?family=Open+Sans:wght@400;600&display=swap">
<style>
  :root {
    --brand-blue: #3277b5;
    --card-black: #1b1b1b;
    --steel-grey: #9d9d9d;
    --text-light: #d6d6d6;
    --backdrop: #2a2a2a;
  }
  * { margin: 0; padding: 0; box-sizing: border-box; }
  html, body {
    width: 1200px;
    height: 900px;
    overflow: hidden;
    background: var(--backdrop);
    font-family: "Open Sans", Arial, sans-serif;
  }
  .canvas {
    position: relative;
    width: 1200px;
    height: 900px;
  }
  .card {
    position: absolute;
    left: 300px;
    width: 600px;
    height: 340px;
    border-radius: 26px;
    background: var(--card-black);
    box-shadow: 0 10px 30px rgba(0,0,0,0.45);
    overflow: hidden;
  }
  .card--front { top: 70px; }
  .card--back { top: 490px; }

  /* Front side */
  .front-brand {
    position: absolute;
    top: 70px;
    left: 0;
    width: 100%;
    display: flex;
    flex-direction: column;
    align-items: center;
    gap: 16px;
  }
  .brand-dot {
    width: 86px;
    height: 86px;
    border-radius: 50%;
    background: var(--steel-grey);
  }
  .front-brand .brand-name {
    font-size: 22px;
    font-weight: 600;
    color: var(--steel-grey);
    letter-spacing: 0.04em;
  }
  .services {
    position: absolute;
    bottom: 34px;
    left: 0;
    width: 100%;
    display: flex;
    justify-content: center;
    gap: 14px;
    list-style: none;
    font-size: 17px;
    color: #ffffff;
  }
  .services li::before {
    content: "";
    display: inline-block;
    width: 8px;
    height: 8px;
    margin-right: 6px;
    border-radius: 50%;
    background: #ffffff;
    vertical-align: middle;
  }

  /* Back side */
  .back-brand {
    position: absolute;
    left: 0;
    top: 0;
    width: 300px;
    height: 100%;
    display: flex;
    flex-direction: column;
    align-items: center;
    justify-content: center;
    gap: 18px;
  }
  .back-brand .brand-dot {
    width: 110px;
    height: 110px;
    background: var(--brand-blue);
  }
  .back-brand .brand-name {
    font-size: 22px;
    font-weight: 600;
    color: var(--brand-blue);
    text-align: center;
    line-height: 1.2;
    letter-spacing: 0.04em;
  }
  .divider {
    position: absolute;
    left: 300px;
    top: 50px;
    width: 1px;
    height: 240px;
    background: linear-gradient(to bottom, transparent, #4a4a4a, transparent);
  }
  .contact {
    position: absolute;
    left: 330px;
    top: 60px;
    color: var(--text-light);
    font-size: 17px;
    line-height: 1.3;
  }
  .contact .person-name {
    font-size: 21px;
    font-weight: 600;
    color: var(--brand-blue);
    text-transform: uppercase;
  }
  .contact .person-role { margin-bottom: 14px; }
  .contact .address { margin-bottom: 14px; }
  .contact-line {
    display: flex;
    align-items: center;
    gap: 8px;
  }
  .contact-line svg { width: 14px; height: 14px; flex: none; }
</style>
</head>
<body>
<main class="canvas">

  <section class="card card--front" aria-label="Card front">
    <div class="front-brand">
      <span class="brand-dot" aria-hidden="true"></span>
      <span class="brand-name">Stonebay Property Group</span>
    </div>
    <ul class="services">
      <li>Construction (commercial &amp; industrial)</li>
      <li>Civil construction</li>
    </ul>
  </section>

  <section class="card card--back" aria-label="Card back">
    <div class="back-brand">
      <span class="brand-dot" aria-hidden="true"></span>
      <span class="brand-name">STONEBAY<br>PROPERTY GROUP</span>
    </div>
    <div class="divider" aria-hidden="true"></div>
    <div class="contact">
      <p class="person-name">Tomas verbick</p>
      <p class="person-role">Project manager</p>
      <p class="address">41 barrow crescent<br>hallam 5291</p>
      <p class="contact-line">
        <svg viewBox="0 0 14 14" aria-hidden="true"><path fill="#3277b5" d="M1 4c0-2 2-3 3-3l1 3-1.5 1c.8 2 2.5 3.7 4.5 4.5L9 8l3 1c0 1-1 3-3 3C5 12 1 8 1 4z"/></svg>
        <span>7306224783</span>
      </p>
      <p class="contact-line">
        <svg viewBox="0 0 14 14" aria-hidden="true"><rect x="3.5" y="1" width="7" height="12" rx="1.2" fill="none" stroke="#3277b5" stroke-width="1.4"/><circle cx="7" cy="11" r="0.8" fill="#3277b5"/></svg>
        <span>(03) 9418 6573</span>
      </p>
      <p class="contact-line">
        <svg viewBox="0 0 14 14" aria-hidden="true"><rect x="1" y="3" width="12" height="8" fill="#3277b5"/><path d="M1 3l6 4.5L13 3" fill="none" stroke="#1b1b1b" stroke-width="1"/></svg>
        <span>Info@verbickgroup.com</span>
      </p>
    </div>
  </section>

</main>
</body>
</html>
```